Hi Designers,

I will need 4 web pages designed. The web page looks like an App (if you click on the logo, or the icon on an iPad, it will take you to the website), but it is still a webpage.

Please check the attachment on this brief to understand what specific pages I need to be designed.

A .PSD (straight-up PhotoShop image) as final deliverable is fine, as long as you give us the exact “web color numbers”.

The design is for desktop and iPad but in a single unified web application, NOT separate web app and (native) iPad app.

Details:

Brightwater Policy Partners is developing a browser-based application for use on any mobile device or desktop. The app will be used by corporations to communicate with their employees regarding legal, regulatory and company requirements for conducting business. The app is known as “Harbor Guidance Portal.” When the user clicks on the icon for Harbor Guidance Portal, they will enter a site full of information that a company deems necessary for the employee to do his/her job. There are several content sections within the site, including a login page, training, policies, forms, news feeds and blogs.

The application has been built using Microsoft .NET, and fully supports CSS-type skinning; it uses traditional page layouts. We are seeking a product logo concept (image), a master application/desktop icon (image), as well as a full color scheme/theme/skin design for all areas of the application (header area, body text, menu bar, etc.) in the form of a CSS. The look should be clean, crisp and professional; nothing cartoony or whimsical. It should be easy to read and “airy”.

We have sketched prototypes for the basic application page layout that we can send as a next step of the process.
Updates

Screen shots have been uploaded to this project.  Please use them to guide your design.

Dear designers,

I apologize for the delay in providing feedback. My partners and I will provide feedback in a few days. Thank you for your patience.

Industry/Entity Type

Business

Font styles to use
Other font styles liked:
• see font on screen shots when uploaded

```html
<!DOCTYPE html>
<html lang="en">
<head>
<meta charset="utf-8">
<title>Harbor Guidance Portal</title>
<link rel="stylesheet" href="https://fonts.googleapis.com/css2?family=Source+Sans+3:wght@400;600&display=swap">
<style>
:root{
  --sky:#08aeea;
  --news:#1a86b8;
  --blog:#0e4a66;
  --forum:#1ca6de;
  --ink:#1e1e1e;
  --muted:#555;
  --date:#a3141a;
  --link:#1a7cb5;
  --heading:#1d5f96;
  --panel-border:#d8d8d8;
  --footer:#2591c0;
  --footer-deep:#1b7db0;
  --orange:#f28a13;
}
*{box-sizing:border-box;margin:0;padding:0}
html,body{width:1032px;height:1200px;overflow:hidden}
body{position:relative;background:#fff;font-family:"Source Sans 3",sans-serif;color:var(--ink);font-size:10.5px;line-height:15.5px}
.abs{position:absolute}

/* header */
.brand{left:103px;top:38px;display:flex;align-items:center;gap:12px}
.brand-mark{width:58px;height:58px;border-radius:50%;background:var(--sky)}
.brand-name{font-size:23px;font-variant:small-caps;color:var(--heading);letter-spacing:.3px}
.nav-rail{left:416px;top:9px;width:344px;height:3px;background:#d4d4d4}
.nav{left:424px;top:23px;display:flex;gap:22px;font-size:11px}
.nav span{display:flex;align-items:center;gap:5px}
.user{left:789px;top:9px;width:131px;height:23px;border:1px solid #cfcfcf;display:flex;align-items:center;gap:6px;padding:0 4px;font-size:9px;color:#777}
.user .avatar{width:20px;height:20px;background:linear-gradient(#d9b48a,#8a5a3a)}
.user .caret{margin-left:auto}
.search{left:568px;top:76px;width:191px;height:21px;border:1px solid #d0d0d0;border-radius:3px;box-shadow:0 2px 3px rgba(0,0,0,.08);font-size:9px;color:#999;padding:3px 8px;display:flex;justify-content:space-between}
.score{left:788px;top:76px;display:flex;height:21px;font-size:14px;color:#fff;border-radius:2px;overflow:hidden}
.score b{font-weight:400;background:#8cc63f;width:25px;text-align:center;line-height:21px}
.score i{font-style:normal;background:linear-gradient(#3b8fd6,#1f5ea8);width:53px;padding-left:9px;line-height:21px}

/* panels */
.panel{border:1px solid var(--panel-border);border-radius:3px;background:linear-gradient(#fff,#fafafa);box-shadow:0 2px 3px rgba(0,0,0,.08);padding:6px}
.bar{height:37px;border-radius:2px;color:#fff;font-size:18px;display:flex;align-items:center;gap:12px;padding:0 12px;text-shadow:0 1px 1px rgba(0,0,0,.3)}
.bar .ico{width:28px;height:26px;border-radius:50%;background:rgba(255,255,255,.85)}
.welcome{left:114px;top:132px;width:812px;height:189px}
.welcome .bar{background:var(--sky)}
.welcome .photo{position:absolute;left:15px;top:60px;width:134px;height:80px;border:3px solid #fff;box-shadow:0 0 0 1px #ddd;background:linear-gradient(135deg,#e7e9ec,#c9cdd2 60%,#e89aa5)}
.welcome .copy{position:absolute;left:167px;top:60px;width:631px}
.welcome .copy p+p{margin-top:15.5px}

.col{top:351px;width:249px;height:362px}
.col-news{left:114px}.col-news .bar{background:var(--news)}
.col-blog{left:399px}.col-blog .bar{background:var(--blog)}
.col-forum{left:678px}.col-forum .bar{background:var(--forum)}
.item{padding:10px 14px 10px 13px;border-bottom:1px solid #ececec;height:101px}
.item:last-child{border-bottom:0}
.date{color:var(--date);font-size:11px;margin-bottom:4px}
.item p{text-align:justify;color:#444}
.src{color:var(--link);margin-top:4px}
.post{display:flex;gap:10px;padding:19px 6px 0 6px;height:103px;border-bottom:1px solid #ececec}
.post:last-child{border-bottom:0}
.thumb{width:56px;height:54px;flex:none;border-radius:3px;border:2px solid #fff;box-shadow:0 1px 3px rgba(0,0,0,.3);background:linear-gradient(135deg,#cfe0ea,#8fa8b8)}
.post .date{margin-bottom:2px}
.post p{color:#444;line-height:14px}

/* lower blocks */
.block{top:748px;width:250px}
.block h2{display:flex;align-items:center;gap:10px;font-weight:400;font-size:16.5px;color:var(--heading);height:40px}
.block h2 .doc{width:26px;height:32px}
.faq-badge{width:38px;height:38px;border-radius:50%;background:radial-gradient(#333,#000);border:3px solid #ccc;color:#fff;font-size:10px;font-weight:600;display:grid;place-items:center}
.block h3{font-weight:400;font-size:15px;font-variant:small-caps;margin:20px 0 10px}
.block p{text-align:justify;line-height:15.5px}
.block .date{margin-top:4px}
.faq{left:118px}.docs{left:402px;width:232px}
.reports{left:685px;top:748px;width:244px}
.reports h2{display:flex;align-items:center;gap:12px;font-weight:400;font-size:16.5px;color:var(--heading);height:40px}
.board{width:100%;margin-top:22px;border-collapse:collapse;font-size:11px}
.board th{font-weight:400;font-size:12px;text-align:left;padding-bottom:4px;border-bottom:1px solid #ccc;color:#333}
.board td{height:27px;font-size:10.5px;padding-top:2px}
.board td:first-child{padding-left:7px}

/* footer */
.links{left:0;top:968px;width:1032px;height:182px;background:var(--footer);color:#fff}
.links h2{position:absolute;left:123px;top:15px;display:flex;align-items:center;gap:12px;font-weight:400;font-size:16.5px}
.link-cols{position:absolute;left:123px;top:60px;display:flex}
.link-cols ul{list-style:none;width:173px}
.link-cols li{font-size:11px;height:20.6px;padding-left:12px;position:relative}
.link-cols li::before{content:"›";position:absolute;left:0;top:-1px}
.legal{left:0;top:1150px;width:1032px;height:50px;background:var(--footer-deep);color:#fff}
.social{position:absolute;left:148px;top:15px;display:flex;gap:8px}
.social span{width:17px;height:17px;border-radius:2px;background:rgba(255,255,255,.35)}
.copyright{position:absolute;right:131px;top:8px;font-size:10.5px}
</style>
</head>
<body>

<header>
  <div class="abs brand"><div class="brand-mark"></div><div class="brand-name">Harbor Guidance Portal</div></div>
  <div class="abs nav-rail"></div>
  <nav class="abs nav">
    <span><svg width="14" height="12" viewBox="0 0 14 12"><path d="M7 0L0 6h2v6h4V8h2v4h4V6h2z" fill="#111"/></svg>Home</span>
    <span><svg width="12" height="14" viewBox="0 0 12 14"><rect x="1" y="1" width="10" height="12" fill="none" stroke="#111" stroke-width="1.5"/><path d="M3 5h6M3 8h6M3 11h6" stroke="#111"/></svg>Menu</span>
    <span><svg width="18" height="12" viewBox="0 0 18 12"><rect x="0" y="2" width="18" height="9" rx="4" fill="#444"/><circle cx="5" cy="6" r="1.5" fill="#ddd"/><circle cx="13" cy="6" r="1.5" fill="#ddd"/></svg>Game</span>
    <span><svg width="14" height="14" viewBox="0 0 14 14"><circle cx="7" cy="7" r="6" fill="#111"/><path d="M7 7V1a6 6 0 0 1 6 6z" fill="#fff"/></svg>HCP 360</span>
  </nav>
  <div class="abs user"><div class="avatar" role="img" aria-label="User avatar"></div>Dana Hale<span class="caret">⌄</span></div>
  <div class="abs search">Search<svg width="14" height="12" viewBox="0 0 14 12"><circle cx="5" cy="5" r="4" fill="none" stroke="#bbb" stroke-width="1.5"/><path d="M8 8l5 4" stroke="#bbb" stroke-width="2"/></svg></div>
  <div class="abs score"><b>1</b><i>427</i></div>
</header>

<section class="abs panel welcome">
  <div class="bar">Welcome to Harbor Guidance Portal</div>
  <div class="photo" role="img" aria-label="Laboratory scientist examining sample dishes"></div>
  <div class="copy">
    <p>Sed ut perspiciatis unde omnis iste natus error sit voluptatem accusantium doloremque laudantium, totam rem aperiam, eaque ipsa quae ab illo inventore veritatis et quasi architecto beatae vitae dicta sunt explicabo.Sed ut perspiciatis unde omnis iste natus error sit voluptatem accusantium doloremque laudantium, totam rem aperiam, eaque ipsa quae ab illo inventore veritatis</p>
    <p>Sed ut perspiciatis unde omnis iste natus error sit voluptatem accusantium doloremque laudantium, totam rem aperiam, eaque ipsa quae ab illo inventore veritatis et quasi architecto beatae vitae dicta sunt explicabo.</p>
  </div>
</section>

<section class="abs panel col col-news">
  <div class="bar"><span class="ico"></span>Compliance News</div>
  <div class="item"><div class="date">Nov 18, 2013</div><p>Sed ut perspiciatis unde omnis iste natus error sit voluptatem accusantium rem aperiam,</p><div class="src">Agency News : Pharma Sector Daily</div></div>
  <div class="item"><div class="date">Nov 18, 2013</div><p>Sed ut perspiciatis unde omnis iste natus error sit voluptatem accusantium rem aperiam,</p><div class="src">Agency News : Pharma Sector Daily</div></div>
  <div class="item"><div class="date">Nov 18, 2013</div><p>Sed ut perspiciatis unde omnis iste natus error sit voluptatem accusantium rem aperiam,</p><div class="src">Agency News : Pharma Sector Daily</div></div>
</section>

<section class="abs panel col col-blog">
  <div class="bar"><span class="ico"></span>Compliance Blog</div>
  <div class="post"><div class="thumb" role="img" aria-label="Researchers working in a lab"></div><div><div class="date">Nov 5, 2013</div><p>Sed ut perspiciatis unde omnis iste natus error sit voluptatem accusantium rem aperiam,</p></div></div>
  <div class="post"><div class="thumb" role="img" aria-label="Scientists at a lab bench"></div><div><div class="date">Nov 5, 2013</div><p>Sed ut perspiciatis unde omnis iste natus error sit voluptatem accusantium rem aperiam,</p></div></div>
  <div class="post"><div class="thumb" role="img" aria-label="Empty laboratory room"></div><div><div class="date">Nov 5, 2013</div><p>Sed ut perspiciatis unde omnis iste natus error sit voluptatem accusantium rem aperiam,</p></div></div>
</section>

<section class="abs panel col col-forum">
  <div class="bar"><span class="ico"></span>Forums</div>
  <div class="item"><div class="date">Nov 18, 2013</div><p>Sed ut perspiciatis unde omnis iste natus error sit voluptatem accusantium rem aperiam,</p><div class="src">Agency News : Pharma Sector Daily</div></div>
  <div class="item"><div class="date">Nov 18, 2013</div><p>Sed ut perspiciatis unde omnis iste natus error sit voluptatem accusantium rem aperiam,</p><div class="src">Agency News : Pharma Sector Daily</div></div>
  <div class="item"><div class="date">Nov 18, 2013</div><p>Sed ut perspiciatis unde omnis iste natus error sit voluptatem accusantium rem aperiam,</p><div class="src">Agency News : Pharma Sector Daily</div></div>
</section>

<section class="abs block faq">
  <h2><span class="faq-badge">FAQ</span>FAQ’s</h2>
  <h3>Mauris Vestibulum Volutpat?</h3>
  <p>Sed ut perspiciatis unde omnis iste natus error sit voluptatem accusantium doloremque laudantium, totam rem aperiam, eaque ipsa quae ab illo inventore veritatis et quasi architecto beatae vitae dicta sunt explicabo.</p>
  <div class="date">Nov 18, 2013</div>
</section>

<section class="abs block docs">
  <h2><svg class="doc" viewBox="0 0 26 32"><path d="M2 1h16l6 6v24H2z" fill="#fff" stroke="#222" stroke-width="1.5"/><path d="M6 11h14M6 15h14M6 19h14M6 23h14M6 27h14" stroke="#222" stroke-width="1.6"/></svg>Document Library</h2>
  <h3>Mauris Vestibulum Volutpat</h3>
  <p>Sed ut perspiciatis unde omnis iste natus error sit voluptatem accusantium doloremque laudantium, totam rem aperiam, eaque ipsa quae ab illo inventore veritatis et quasi architecto beatae vitae dicta sunt explicabo.</p>
  <div class="date">Nov 18, 2013</div>
</section>

<section class="abs reports">
  <h2><svg class="doc" width="26" height="32" viewBox="0 0 26 32"><path d="M2 1h16l6 6v24H2z" fill="#fff" stroke="#222" stroke-width="1.5"/><path d="M6 11h14M6 15h14M6 19h14M6 23h14M6 27h14" stroke="#222" stroke-width="1.6"/></svg>Reports</h2>
  <table class="board">
    <thead><tr><th>Rank</th><th>Player</th><th>Score</th><th>%</th></tr></thead>
    <tbody>
      <tr><td>4</td><td>Leo.K</td><td>456</td><td>88</td></tr>
      <tr><td>4</td><td>Tara.B</td><td>456</td><td>88</td></tr>
      <tr><td>4</td><td>Tara.B</td><td>456</td><td>88</td></tr>
      <tr><td>4</td><td>Tara.B</td><td>456</td><td>88</td></tr>
    </tbody>
  </table>
</section>

<footer>
  <div class="abs links">
    <h2><svg width="32" height="32" viewBox="0 0 32 32"><g fill="none" stroke="#2b2b2b" stroke-width="4"><rect x="3" y="15" width="16" height="9" rx="4.5" transform="rotate(-45 11 19.5)"/><rect x="13" y="8" width="16" height="9" rx="4.5" transform="rotate(-45 21 12.5)"/></g></svg>Relevant Links</h2>
    <div class="link-cols">
      <ul><li>Loreum Ipsum</li><li>Sed Erat</li><li>Nunc get mauris</li><li>Aenan Adpicing</li><li>Phasellus</li></ul>
      <ul><li>Loreum Ipsum</li><li>Sed Erat</li><li>Nunc get mauris</li><li>Aenan Adpicing</li><li>Phasellus</li></ul>
      <ul><li>Loreum Ipsum</li><li>Sed Erat</li><li>Nunc get mauris</li><li>Aenan Adpicing</li><li>Phasellus</li></ul>
      <ul><li>Loreum Ipsum</li><li>Sed Erat</li><li>Nunc get mauris</li><li>Aenan Adpicing</li><li>Phasellus</li></ul>
      <ul><li>Loreum Ipsum</li><li>Sed Erat</li><li>Nunc get mauris</li><li>Aenan Adpicing</li><li>Phasellus</li></ul>
    </div>
  </div>
  <div class="abs legal">
    <div class="social"><span></span><span></span><span></span><span></span><span></span><span></span></div>
    <div class="copyright">© 2013 HarborGuidancePortal, All Rights Reserved</div>
  </div>
</footer>

</body>
</html>
```